Industrial Project Sign

We need an eye catching (but professional) industrial project sign that will be very large (roughly 12' high x 18' wide). This sign will be highly visible from the adjacent high speed highway.

* The following needs to be at the bottom of the signage: Logo (uploaded), Name (Brightline Property Partners, Inc.) (uploaded) and phone number (415)736-2958

*Name of Project - "Meridale Commerce Park"

* Text items
Land for Sale
Build to Suit
Zoning: Industrial (G I & L I)

* Interesting background that is eye catching
Updates

Good morning all,

We are considering all designers options as we go and are waiting for the final designs to come in by the 4th so that we can give each one a good look.   If you have any new designs, questions, further design options or any tweeks you want to do to current designs, please do so at this time.

Thanks to all of you for your submissions.

Industry/Entity Type

Industrial

```html
<!DOCTYPE html>
<html lang="en">
<head>
<meta charset="utf-8">
<title>Brightline Property Partners – Meridale Commerce Park Sign</title>
<link rel="stylesheet" href="https://fonts.googleapis.com/css2?family=Oswald:wght@700&family=Roboto:wght@700&display=swap">
<style>
  :root {
    --maroon: #3a0000;
    --white: #ffffff;
    --canvas: #ffffff;
  }
  html, body {
    margin: 0;
    padding: 0;
    overflow: hidden;
    background: var(--canvas);
  }
  .canvas {
    position: relative;
    width: 1200px;
    height: 1000px;
    overflow: hidden;
    background: var(--canvas);
  }
  .canvas > svg { display: block; }
  .sign-bg { fill: var(--maroon); }
  .sign-band { fill: var(--white); }
  .brand-mark { fill: var(--maroon); }
  .project-name {
    fill: var(--maroon);
    font-family: "Oswald", "Arial Narrow", sans-serif;
    font-weight: 700;
    font-size: 34px;
  }
  .brand-name {
    fill: var(--maroon);
    font-family: "Roboto", Arial, sans-serif;
    font-weight: 700;
    font-size: 17px;
  }
  .headline {
    fill: var(--white);
    font-family: "Oswald", "Arial Narrow", sans-serif;
    font-weight: 700;
  }
  .headline-primary { font-size: 122px; }
  .headline-secondary { font-size: 112px; }
  .zoning {
    fill: var(--white);
    font-family: "Roboto", Arial, sans-serif;
    font-weight: 700;
    font-size: 40px;
  }
  .phone-panel { fill: var(--white); }
  .phone {
    fill: var(--maroon);
    font-family: "Oswald", "Arial Narrow", sans-serif;
    font-weight: 700;
    font-size: 62px;
  }
</style>
</head>
<body>
<div class="canvas">
  <svg width="1200" height="1000" viewBox="0 0 1200 1000" xmlns="http://www.w3.org/2000/svg">
    <defs>
      <g id="project-sign">
        <rect class="sign-bg" x="0" y="0" width="811" height="541"/>
        <path class="sign-band" d="M3,53 Q405,-23 808,53 L808,133 Q405,213 3,133 Z"/>
        <rect class="brand-mark" x="380" y="32" width="52" height="52"/>
        <text class="project-name" x="405.5" y="128" text-anchor="middle">MERIDALE COMMERCE PARK</text>
        <text class="brand-name" x="405.5" y="160" text-anchor="middle" textLength="266" lengthAdjust="spacingAndGlyphs">Brightline Property Partners, Inc.</text>
        <text class="headline headline-primary" x="405.5" y="292" text-anchor="middle" textLength="696" lengthAdjust="spacingAndGlyphs">LAND FOR SALE</text>
        <text class="headline headline-secondary" x="405.5" y="392" text-anchor="middle" textLength="702" lengthAdjust="spacingAndGlyphs">BUILD TO SUIT</text>
        <text class="zoning" x="405.5" y="440" text-anchor="middle" textLength="713" lengthAdjust="spacingAndGlyphs">ZONING: INDUSTRIAL (G I &amp; L I)</text>
        <rect class="phone-panel" x="3" y="455" width="805" height="76"/>
        <text class="phone" x="405.5" y="518" text-anchor="middle" textLength="602" lengthAdjust="spacingAndGlyphs">Phone :(415) 736-2958</text>
      </g>
    </defs>
    <use href="#project-sign" transform="translate(194,37)"/>
    <use href="#project-sign" transform="translate(844,744) scale(0.3946)"/>
  </svg>
</div>
</body>
</html>
```